Sell the dream! Property investment proposal document

We are looking for a proposal document which outlines our vision for property development. The purpose of the document is to raise investment from investors - sell the dream!
Brief summary:
Kestrel Dwellings Developments, is an emerging New Zealand property investment company with a focus on providing unique property investment opportunities.
Our expertise and capabilities in architectural modular homes provide us with a remarkable advantage in tackling the development of properties that are typically considered challenging, remote, or uniquely positioned.
Our specialization in this niche sector of property development not only sets us apart from competitors, but also paves the way for lucrative investment opportunities in the New Zealand property market.
Feel free to use any images from www.kestreldwellings.co.nz
Target Market(s)
investors for a unique property development opportunity
Industry/Entity Type
luxury property development in unique locations throughout New Zealand
Colors
Designer to choose only greyscale colors for use in the design.
Look and feel

```html
<!DOCTYPE html>
<html lang="en">
<head>
<meta charset="utf-8">
<title>Kestrel Dwellings – Investment Proposal</title>
<link href="https://fonts.googleapis.com/css2?family=Jost:wght@300;400;500&display=swap" rel="stylesheet">
<style>
:root{
  --backdrop:#96979b;
  --page:#000;
  --ink:#fff;
  --panel:#111;
  --ghost:#1c1c1c;
  --label:#1a1a1a;
  --box:#f2f2f2;
  --body:#e6e6e6;
}
*{margin:0;padding:0;box-sizing:border-box}
html,body{width:1200px;height:2284px;overflow:hidden}
body{background:var(--backdrop);font-family:'Jost',sans-serif;position:relative;color:var(--ink)}
.page-label{position:absolute;width:468px;text-align:center;font-size:18px;color:var(--label);font-weight:400}
.page{position:absolute;width:468px;height:663px;background:var(--page);overflow:hidden;box-shadow:0 18px 18px -10px rgba(0,0,0,.35)}
.page.inner{background:var(--panel)}
.page.inner::before{content:"";position:absolute;left:0;right:0;top:0;height:22px;background:var(--page)}
.col-left{left:103px}.col-right{left:628px}
.row-1{top:91px}.row-2{top:809px}.row-3{top:1530px}
.photo{position:absolute}
.brand-mark{position:absolute;display:flex;align-items:center;gap:8px;font-weight:500;font-size:13px;line-height:1;color:var(--ink);letter-spacing:.3px}
.brand-mark .square{width:9px;height:9px;background:var(--ink)}
.brand-top{top:30px;left:50%;transform:translateX(-50%)}
.brand-bottom{bottom:20px;left:50%;transform:translateX(-50%)}
.ghost-name{position:absolute;font-weight:400;color:var(--ghost);white-space:nowrap;line-height:1}
.heading-box{position:absolute;background:var(--box);color:#000;font-weight:500;font-size:22px;line-height:31px;height:31px}
.heading-box.first{text-align:right;padding-right:10px}
.heading-box.second{padding-left:10px}
.copy{position:absolute;font-weight:300;color:var(--body)}
.copy p{margin-bottom:8px}
/* back cover */
.back .ghost-name{font-size:150px;transform:rotate(-90deg);transform-origin:left top;left:12px;top:600px}
.back .cover-name{position:absolute;top:280px;left:0;width:100%;text-align:center;font-size:78px;font-weight:400;padding-left:40px;letter-spacing:-1px}
.contact{position:absolute;bottom:20px;width:100%;text-align:center;font-size:13px;line-height:21px;font-weight:300}
/* front cover */
.front .cover-photo{left:35px;top:133px;width:399px;height:336px;background:linear-gradient(180deg,#c9ccc9 0%,#6f7a6a 45%,#2a2e27 75%,#5e6f48 100%)}
.front .cover-name{position:absolute;top:400px;width:100%;text-align:center;font-size:104px;font-weight:400;letter-spacing:-2px;line-height:1}
.front .tagline{position:absolute;top:560px;width:100%;text-align:center;font-size:30px;letter-spacing:7px;font-weight:400}
.front .url{position:absolute;bottom:12px;width:100%;text-align:center;font-size:12px;font-weight:300}
.wide-photo{left:0;top:22px;width:468px}
/* page 1 */
.p1 .wide-photo{height:269px;background:linear-gradient(180deg,#8d8f93 0%,#c8c8c8 40%,#555 70%,#8a8c90 100%)}
.p1 .copy{left:59px;top:374px;width:351px;font-size:7.4px;line-height:11px}
/* page 2 */
.p2{background:var(--page)}
.p2 .photo-top{left:204px;top:22px;width:264px;height:309px;background:linear-gradient(180deg,#5c4a36 0%,#b7b0a6 40%,#8d8a84 70%,#4a4540 100%)}
.p2 .photo-bottom{left:204px;top:333px;width:264px;height:330px;background:linear-gradient(90deg,#2a2826 0%,#6b665f 45%,#c9c9c6 65%,#4d4c4a 100%)}
.p2 .heading-box{font-size:21px}
.p2 .copy{left:19px;top:102px;width:175px;font-size:7px;line-height:13.3px;text-align:justify}
.p2 .copy p{margin-bottom:13px}
.p2 .ghost-name{left:22px;top:550px;font-size:54px;color:#2a2a2a}
.p2 .photo-name{position:absolute;left:435px;top:636px;transform:rotate(-90deg);transform-origin:left top;font-size:56px;font-weight:400;line-height:1;white-space:nowrap}
.p2 .brand-bottom{left:24px;transform:none}
/* page 3 & 4 */
.p3 .wide-photo,.p4 .wide-photo{height:322px}
.p3 .wide-photo{background:linear-gradient(180deg,#c7c9c6 0%,#3c3e3a 30%,#2a2b28 60%,#8a7a52 100%)}
.p4 .wide-photo{background:linear-gradient(180deg,#eef0ef 0%,#b8c4c9 40%,#6f7d55 65%,#9c8d6e 100%)}
.p3 .copy{left:65px;top:452px;width:340px;font-size:7.4px;line-height:18px}
.p3 .ghost-name{font-size:74px;color:#2a2a2a;transform:rotate(-90deg);transform-origin:left top;left:400px;top:663px}
.p4 .copy{left:37px;top:422px;width:396px;font-size:7.2px;line-height:15.6px;text-align:justify}
</style>
</head>
<body>

<div class="page-label col-left" style="top:59px">Back</div>
<div class="page-label col-right" style="top:59px">Front</div>
<div class="page-label col-left" style="top:782px">Page 1</div>
<div class="page-label col-right" style="top:782px">Page 2</div>
<div class="page-label col-left" style="top:1503px">Page 3</div>
<div class="page-label col-right" style="top:1503px">Page 4</div>

<!-- Back cover -->
<section class="page back col-left row-1">
  <div class="brand-mark brand-top"><span class="square"></span>Kestrel Dwellings</div>
  <div class="ghost-name">Kestrel</div>
  <div class="cover-name">Kestrel</div>
  <div class="contact">Ph: 09 555 0142<br>Web: www.kestreldwellings.co.nz</div>
</section>

<!-- Front cover -->
<section class="page front col-right row-1">
  <div class="brand-mark brand-top"><span class="square"></span>Kestrel Dwellings</div>
  <div class="photo cover-photo" role="img" aria-label="Dark slatted modular house among trees with a timber deck and lawn"></div>
  <div class="cover-name">Kestrel</div>
  <div class="tagline">Sell the dream!</div>
  <div class="url">www.kestreldwellings.co.nz</div>
</section>

<!-- Page 1 -->
<section class="page inner p1 col-left row-2">
  <div class="photo wide-photo" role="img" aria-label="Open-plan living room with white sofas, dark timber walls and a view to the garden"></div>
  <div class="heading-box first" style="left:39px;top:300px;width:191px">Business</div>
  <div class="heading-box second" style="left:230px;top:331px;width:204px">Overview</div>
  <div class="copy">
    <p>Kestrel Dwellings Developments, is an emerging New Zealand property investment company with a focus on providing unique property investment opportunities.</p>
    <p>Our expertise and capabilities in architectural modular homes provide us with a remarkable advantage in tackling the development of properties that are typically considered challenging, remote, or uniquely positioned.</p>
    <p>As a company, with 48 employees boasting a wealth of experience in handling complex architectural projects, making us well-equipped to navigate the intricacies and demands of such ventures.</p>
    <p>This advantage allows us to not only execute projects efficiently but also to deliver exceptional results within condensed time frames.</p>
    <p>By capitalizing on our ability to develop difficult, remote, or one-of-a-kind properties swiftly and effectively, Kestrel Dwellings Developments offers investors a rare chance to engage in projects that promise exceptional profitability in the New Zealand property market.</p>
    <p>Our specialization in this niche sector of property development not only sets us apart from competitors, but also paves the way for lucrative investment opportunities in the New Zealand property market.</p>
  </div>
  <div class="brand-mark brand-bottom"><span class="square"></span>Kestrel Dwellings</div>
</section>

<!-- Page 2 -->
<section class="page p2 col-right row-2">
  <div class="photo photo-top" role="img" aria-label="Dining and living space with timber ceiling, skylights and sea view"></div>
  <div class="photo photo-bottom" role="img" aria-label="Bathroom with freestanding bath, timber slats and a window to the landscape"></div>
  <div class="heading-box first" style="left:0;top:22px;width:111px">Business</div>
  <div class="heading-box second" style="left:113px;top:54px;width:91px">Origins</div>
  <div class="copy">
    <p>Kestrel Dwellings Developments was established with the goal of transforming the property investment market in New Zealand by introducing an innovative approach that centers on architectural modular designs and streamlined project timelines.</p>
    <p>Driven by our enthusiasm for architecture and real estate, we have expanded our successful business model to not only offer financial opportunities for investors but also to expand on our passion for high-end architectural design.</p>
    <p>With a wealth of experience accumulated over the past six years in the construction and the property market, we are pivoting to focus solely on our property development initiatives, presenting completed Kestrel projects to the market, in exclusive locations.</p>
    <p>These projects will boast high-quality standards, meticulous attention to detail and landscaping, and creative design elements.</p>
    <p>By introducing completed Kestrel properties into the market, we aim to reach a wider audience, catering to individuals who prefer ready-to-occupy homes, over engaging in the design and construction process. This approach also simplifies the financing process for prospective buyers, as established properties are often preferred by financial lenders.</p>
  </div>
  <div class="ghost-name">Kestrel</div>
  <div class="photo-name">Kestrel</div>
  <div class="brand-mark brand-bottom"><span class="square"></span>Kestrel Dwellings</div>
</section>

<!-- Page 3 -->
<section class="page inner p3 col-left row-3">
  <div class="photo wide-photo" role="img" aria-label="Dark pavilion home with outdoor dining area and grasses in the foreground"></div>
  <div class="heading-box first" style="left:37px;top:372px;width:191px">Competitive</div>
  <div class="heading-box second" style="left:229px;top:403px;width:203px">Advantage</div>
  <div class="copy">
    <p>Our competitive advantage lies in the uniqueness of our property investment opportunities. Unlike traditional real estate companies, we focus on offering properties that are not only profitable but also aesthetically pleasing and unique. By catering to the tastes of architecture lovers, we set ourselves apart from the competition and attract a niche market of customers who appreciate the artistry and design of our projects.</p>
    <p>Additionally, the streamlined and condensed timelines facilitated by our modular approach provide quicker returns on investment.</p>
  </div>
  <div class="ghost-name">Kestrel</div>
  <div class="brand-mark brand-bottom"><span class="square"></span>Kestrel Dwellings</div>
</section>

<!-- Page 4 -->
<section class="page inner p4 col-right row-3">
  <div class="photo wide-photo" role="img" aria-label="Floor-to-ceiling glazing looking out over green hills and a harbour"></div>
  <div class="heading-box first" style="left:37px;top:352px;width:191px">Financial</div>
  <div class="heading-box second" style="left:229px;top:383px;width:203px">Summary</div>
  <div class="copy">
    <p>In terms of financial projections, with each development, we anticipate a profit of 10%-20% which will be project dependent.</p>
    <p>This growth is fueled by the increasing demand for unique property investments in New Zealand and our ability to deliver high-quality services to the market in a condensed time frame, with heavily controlled costs.</p>
    <p>With a solid business model and a dedicated team, we are confident in our ability to achieve success and establish Kestrel Dwellings Investments as a trusted name in the industry.</p>
    <p>New Zealand's property market has been experiencing steady growth over the years, making it an attractive destination for property investors. With its beautiful landscapes and strong economy, New Zealand offers a diverse range of investment opportunities for both local and international investors. The demand for quality properties in prime locations continues to rise, creating a favorable environment for property investment companies like ours that can lean on our modular benefits of being able to reach unique and remote locations.</p>
  </div>
  <div class="brand-mark brand-bottom"><span class="square"></span>Kestrel Dwellings</div>
</section>

</body>
</html>
```